Digital Marketing Website Redesign, modern, fresh, dynamic

Hi there, we would like to freshen up our website and create a new dynamic look. We are a digital marketing agency who specialise in digital transformation in the form of creating websites for appointment bookings. Our clients are service businesses such as hairdressers, dentists and doctors who's patients need to book appointments with them.

Our company name is Tallomex with the point being we can help increase your revenue curve by increasing your appointment bookings.

Our services include building the website, creating campaigns to drive traffic, increasing conversions and monitoring and reporting.

We are playing with a tagline of 'Step into your Digital Transformation' as we have a 5 step journey that customers can take with us getting them from zero to full appointment bookings.

Our current website is www.tallomex-sample.com

You can see a draft design that I mocked up on Canva here https://www.draftboard-sample.com/design/QXB82LmpR7T/KpoW39dnFsYbZet_wqe_OPa/edit?utm_content=QXB82LmpR7T&utm_campaign=designshare&utm_medium=link2&utm_source=sharebutton

Also attached some other homepage ideas. In regard to photos we are open to ideas.

Please let if you need any more information to provide us with an initial design. Thanks million and I look forward to receiving fantastic designs :)

Marian Dobbs
Tallomex

Target Market(s)

Appointment based businesses such as hairdressers, dentists, doctors

Industry/Entity Type

Marketing and Digital

Coding

Coded - Design and coding required

Number of Pages Required

1 page

Colors
0094D4
00A9DD
6FCCEA
C7EBF8
E9F6FB

Requirements
Must have
• Appointment booking CTA
Nice to have
• A website we like https://www.fergalwhitty-sample.ie

```html
<!DOCTYPE html>
<html lang="en">
<head>
<meta charset="utf-8">
<title>Tallomex – Step into your Digital Transformation</title>
<link href="https://fonts.googleapis.com/css2?family=Poppins:ital,wght@0,400;0,500;0,600;0,700;1,400&display=swap" rel="stylesheet">
<style>
:root{
  --blue:#0094D4;
  --blue-2:#00A9DD;
  --blue-3:#6FCCEA;
  --blue-4:#C7EBF8;
  --blue-5:#E9F6FB;
  --navy:#0c1b33;
  --ink:#0f1a2b;
  --text:#3a4454;
  --white:#fff;
}
*{box-sizing:border-box;margin:0;padding:0}
html,body{width:1200px;height:3957px;overflow:hidden}
body{font-family:'Poppins',sans-serif;color:var(--ink);background:var(--white);position:relative}
.abs{position:absolute}
.btn{position:absolute;display:flex;align-items:center;justify-content:center;background:var(--blue);color:#fff;font-weight:600;border-radius:30px;font-size:14px}

/* nav */
.nav{position:absolute;left:0;top:0;width:1200px;height:83px;background:#fff}
.brand{position:absolute;left:83px;top:24px;font-size:25px;font-weight:600;color:var(--blue);display:flex;align-items:center;gap:8px}
.brand i{width:12px;height:12px;border-radius:50%;background:var(--blue-2);display:block}
.menu{position:absolute;left:392px;top:33px;display:flex;gap:34px;font-size:14px;color:var(--ink)}

/* hero */
.hero{position:absolute;left:0;top:83px;width:1200px;height:667px;background:radial-gradient(ellipse at 60% 45%,#3a8fb0 0%,#1b4a66 25%,#0d2233 55%,#070f1a 100%)}
.hero h1{position:absolute;left:83px;top:305px;font-size:51px;line-height:68px;font-weight:600;color:#fff}
.hero p{position:absolute;left:83px;top:458px;width:780px;font-size:14px;line-height:23px;color:#fff}
.dots{position:absolute;left:1101px;top:518px}
.dots span{display:block;width:8px;height:8px;border-radius:50%;background:rgba(255,255,255,.25);margin:0 auto 18px}
.dots span.on{width:14px;height:14px;background:var(--blue-2);border:2px solid #fff}

/* stats */
.stat{position:absolute;top:837px;width:240px}
.stat svg{display:block}
.stat b{display:block;font-size:46px;font-weight:600;line-height:1;margin-top:24px}
.stat span{display:block;font-size:14px;margin-top:18px;color:var(--ink)}

/* reviews */
.h2{font-size:42px;font-weight:600;color:var(--ink)}
.arrow{position:absolute;top:1058px;width:40px;height:40px;border-radius:50%;background:var(--blue);display:flex;align-items:center;justify-content:center}
.review{position:absolute;top:1141px;width:326px;height:257px;background:#fff;border-radius:18px;box-shadow:0 6px 24px rgba(0,40,80,.07);padding:24px}
.stars{color:#f6b21b;font-size:15px;letter-spacing:3px}
.review p{font-style:italic;font-size:13.5px;line-height:23px;color:var(--text);margin-top:16px}
.review .who{font-size:13.5px;font-weight:600;color:var(--blue);margin-top:16px}

/* services */
.service{position:absolute;top:1484px;width:400px;height:378px;text-align:center;color:#fff}
.service h3{margin-top:92px;font-size:29px;font-weight:600}
.service p{width:330px;margin:18px auto 0;font-size:14px;line-height:23px}
.service .btn{left:148px;top:242px;width:105px;height:45px}

/* steps */
.steps{position:absolute;left:0;top:1862px;width:1200px;height:680px;background:var(--blue-5)}
.pill{position:absolute;top:185px;width:97px;height:36px;border-radius:20px;background:#fff;font-size:13px;font-weight:600;display:flex;align-items:center;justify-content:center}
.pill.on{background:var(--blue);color:#fff}
.link{position:absolute;top:202px;width:74px;height:3px;background:var(--blue-4)}
.stepcard{position:absolute;left:83px;top:264px;width:1032px;height:332px;background:#fff;border-radius:22px;overflow:hidden}
.stepcard h3{position:absolute;left:528px;top:44px;font-size:29px;font-weight:600}
.stepcard p{position:absolute;left:528px;top:100px;width:450px;font-size:13.5px;line-height:23px;color:var(--text)}

/* team */
.member{position:absolute;top:2791px;width:300px;height:348px;color:#fff;text-align:center}
.member b{position:absolute;left:0;right:0;top:274px;font-size:20px;font-weight:600}
.member span{position:absolute;left:0;right:0;top:304px;font-size:13.5px}

/* cta */
.cta{position:absolute;left:0;top:3139px;width:1200px;height:446px;background:linear-gradient(90deg,#0a8fd0 0%,#0f9ad8 40%,rgba(40,160,220,.7) 62%,#c9d8e2 100%)}
.cta h2{position:absolute;left:83px;top:96px;font-size:42px;line-height:60px;font-weight:600;color:#fff}
.cta p{position:absolute;left:83px;top:228px;width:480px;font-size:13.5px;line-height:23px;color:#fff}

/* footer */
.footer{position:absolute;left:0;top:3585px;width:1200px;height:372px;background:var(--navy);color:#fff}
.footer h4{position:absolute;top:90px;font-size:20px;font-weight:600}
.footer .txt{position:absolute;font-size:13.5px;line-height:23px}
.input{position:absolute;left:789px;top:84px;width:326px;height:51px;border-radius:8px;background:#1d2c45;font-size:13.5px;color:#c2cad6;padding:16px 26px}
.copy{position:absolute;left:0;right:0;top:324px;text-align:center;font-size:13.5px;color:#cfd6e0}
</style>
</head>
<body>

<header class="nav">
  <div class="brand">Tallomex<i></i></div>
  <nav class="menu"><span>5 Steps</span><span>Our Pricing</span><span>Ahead of the Curve</span><span>Our Team</span></nav>
  <div class="btn" style="left:911px;top:18px;width:204px;height:45px">Book an Appointment</div>
</header>

<section class="hero" role="img" aria-label="Person walking into a glowing digital tunnel of light lines">
  <h1>Step into your Digital<br>Transformation</h1>
  <p>Digital transformation is a journey. At Tallomex we divide the journey into five key steps that take your business from comprehensive market research to full appointment bookings. Ready to go on that journey?</p>
  <div class="btn" style="left:83px;top:537px;width:123px;height:45px">Start Here</div>
  <div class="dots"><span class="on"></span><span></span><span></span></div>
</section>

<div class="stat" style="left:83px">
  <svg width="26" height="26" viewBox="0 0 26 26"><rect x="2" y="2" width="22" height="16" rx="4" fill="var(--blue)"/><rect x="8" y="8" width="12" height="2" fill="#fff"/><circle cx="6" cy="21" r="4" fill="none" stroke="var(--blue)" stroke-width="2"/></svg>
  <b>762</b><span>Appointments Booked</span>
</div>
<div class="stat" style="left:347px">
  <svg width="26" height="26" viewBox="0 0 26 26"><path d="M2 4h18v14H9l-5 5v-5H2z" fill="var(--blue)"/><circle cx="7" cy="11" r="1.5" fill="#fff"/><circle cx="11" cy="11" r="1.5" fill="#fff"/><circle cx="15" cy="11" r="1.5" fill="#fff"/><circle cx="22" cy="3" r="3" fill="none" stroke="var(--blue)" stroke-width="2"/></svg>
  <b>31</b><span>Marketing Campaigns</span>
</div>
<div class="stat" style="left:611px">
  <svg width="26" height="26" viewBox="0 0 26 26"><rect x="1" y="1" width="24" height="24" rx="6" fill="var(--blue)"/><path d="M6 17l5-5 3 3 6-6" stroke="#fff" stroke-width="2" fill="none"/></svg>
  <b>25%</b><span>Website Traffic Increase</span>
</div>
<div class="stat" style="left:876px">
  <svg width="26" height="26" viewBox="0 0 26 26"><path d="M3 23L17 9" stroke="var(--blue)" stroke-width="3"/><path d="M20 2v6M17 5h6M8 3v4M6 5h4M21 15v4M19 17h4" stroke="var(--blue-2)" stroke-width="2"/></svg>
  <b>762</b><span>Creative Ideas</span>
</div>

<h2 class="h2 abs" style="left:98px;top:1050px">Why others choose us?</h2>
<div class="arrow" style="left:1019px"><svg width="16" height="16" viewBox="0 0 16 16"><path d="M13 8H3M7 4L3 8l4 4" stroke="#fff" stroke-width="1.8" fill="none"/></svg></div>
<div class="arrow" style="left:1075px"><svg width="16" height="16" viewBox="0 0 16 16"><path d="M3 8h10M9 4l4 4-4 4" stroke="#fff" stroke-width="1.8" fill="none"/></svg></div>

<article class="review" style="left:83px"><div class="stars">★★★★★</div><p>Having had to close for Covid-19 in March 2020, Tallomex's Online Booking System really helped us as within a few days of the Swiss announcement that we could re-open in May we received over 100 appointment reservations..</p><div class="who">Lena Hartwig, Owner, Salon Veda Zug</div></article>
<article class="review" style="left:436px"><div class="stars">★★★★★</div><p>Having had to close for Covid-19 in March 2020, Tallomex's Online Booking System really helped us as within a few days of the Swiss announcement that we could re-open in May we received over 100 appointment reservations..</p><div class="who">Lena Hartwig, Owner, Salon Veda Zug</div></article>
<article class="review" style="left:788px"><div class="stars">★★★★★</div><p>Having had to close for Covid-19 in March 2020, Tallomex's Online Booking System really helped us as within a few days of the Swiss announcement that we could re-open in May we received over 100 appointment reservations..</p><div class="who">Lena Hartwig, Owner, Salon Veda Zug</div></article>

<div class="service" style="left:0;background:linear-gradient(180deg,#5a6a7a,#2a3340)" role="img" aria-label="Team planning a campaign with sticky notes on a desk">
  <h3>Creative Campaigns</h3><p>Digital transformation is a journey. At Tallomex we divide the journey into five key steps that take your business from comprehensive.</p><div class="btn">Sign Up</div>
</div>
<div class="service" style="left:400px;background:linear-gradient(180deg,#6a6e74,#2e3238)" role="img" aria-label="Colleagues reviewing research charts at a table">
  <h3>Market Research</h3><p>Digital transformation is a journey. At Tallomex we divide the journey into five key steps that take your business from comprehensive.</p><div class="btn">Sign Up</div>
</div>
<div class="service" style="left:800px;background:linear-gradient(180deg,#7a7670,#2f2e2c)" role="img" aria-label="Person booking online on a laptop">
  <h3>Online Bookings</h3><p>Digital transformation is a journey. At Tallomex we divide the journey into five key steps that take your business from comprehensive.</p><div class="btn">Sign Up</div>
</div>

<section class="steps">
  <h2 class="h2 abs" style="left:0;right:0;top:86px;text-align:center;font-size:40px">5 Steps</h2>
  <div class="pill on" style="left:138px">Step 01</div><div class="link" style="left:252px"></div>
  <div class="pill" style="left:342px">Step 02</div><div class="link" style="left:458px"></div>
  <div class="pill" style="left:549px">Step 03</div><div class="link" style="left:664px"></div>
  <div class="pill" style="left:755px">Step 04</div><div class="link" style="left:870px"></div>
  <div class="pill" style="left:961px">Step 05</div>
  <div class="stepcard">
    <div class="abs" style="left:0;top:0;width:504px;height:332px;background:linear-gradient(135deg,#8a8f92,#6e7376)" role="img" aria-label="Overhead view of a desk with tablet and phone showing a booking site"></div>
    <h3>Online Readiness Review</h3>
    <p>From business management and web development to creative campaign delivery and social media expertise, our team has all the experience your business needs to it to the top of its digital game. From business management and web development to creative campaign delivery and social media expertise, our team has all the experience your business needs to it to the top of its digital game.</p>
  </div>
</section>

<h2 class="h2 abs" style="left:0;right:0;top:2628px;text-align:center">Our Team</h2>
<p class="abs" style="left:200px;width:800px;top:2702px;text-align:center;font-size:13.5px;line-height:23px;color:var(--text)">From business management and web development to creative campaign delivery and social media expertise, our team has all the experience your business needs to it to the top of its digital game.</p>

<div class="member" style="left:0;background:linear-gradient(180deg,#9aa0a6,#3b4048)" role="img" aria-label="Portrait of Declan, account manager"><b>Declan</b><span>Account Manager</span></div>
<div class="member" style="left:300px;background:linear-gradient(180deg,#8a7d74,#3a3330)" role="img" aria-label="Portrait of Sophie, account manager"><b>Sophie</b><span>Account Manager</span></div>
<div class="member" style="left:600px;background:linear-gradient(180deg,#cfc8c0,#2e2a28)" role="img" aria-label="Portrait of Maria, account manager"><b>Maria</b><span>Account Manager</span></div>
<div class="member" style="left:900px;background:linear-gradient(90deg,#e88a2e,#b9a89a)" role="img" aria-label="Portrait of Niamh, account manager"><b>Niamh</b><span>Account Manager</span></div>

<section class="cta" role="img" aria-label="Woman working at a desktop computer in a bright office with sticky notes">
  <h2>Start your Digital<br>Transformation</h2>
  <p>Digital transformation is a journey. At Tallomex we divide the journey into five key steps that take your business from comprehensive market research to full appointment bookings. Ready to go on that journey?</p>
  <div class="btn" style="left:83px;top:317px;width:196px;height:45px;background:var(--navy)">Book a Appointment</div>
</section>

<footer class="footer">
  <h4 style="left:83px">Tallomex Limited</h4>
  <div class="txt" style="left:83px;top:146px;width:330px">Harbourgate Business Centre, Northfield Technical Campus, Kilbrannan, Co. Westmere<br>Ireland X00 A1BC</div>
  <h4 style="left:436px">Opening Hours</h4>
  <div class="txt" style="left:436px;top:146px">Monday - Friday</div>
  <div class="txt" style="left:644px;top:146px">8.30am - 6.30pm</div>
  <div class="txt" style="left:436px;top:186px">Saturday and Sunday</div>
  <div class="txt" style="left:715px;top:186px">Closed</div>
  <div class="input">Email Address</div>
  <div class="btn" style="left:789px;top:154px;width:326px;height:46px">Subscribe Now</div>
  <div class="copy">Copyright © 2024 <b>Tallomex</b> · All Rights Reserved</div>
</footer>

</body>
</html>
```